Call Center In Need of Website Design

We are a call center that provides inbound and outbound calling & marketing services for eCommerce store. We would like to see a fun, creative, playful design that is simple.

Here are some sample design sites we like;
- https://www.velmoreline.com/
- https://pindrask.io/
- https://www.glimbertic.com/live-chat-software/
- https://www.zavrolin.com/

Here are some competitor sites;
- https://www.ostrevaglinks.com/
- https://www.helpkestrel.com/

I have attached website content for your use.

Target Market(s)

eCommerce

Coding

Coded - Design and coding required

Number of Pages Required

5+ page

Font styles to use
Sans Serif

Colors

Designer to choose colors to be used in the design.

Requirements
Must have
• Must have designs for the following 5 separate pages;
• 1. Home (landing)
• - This will be were the design style really needs to show.
• - Just needs to touch on key services
• - CTA
• 2. About Us
• - Basic page for about me paragraph
• 3. Services
• - List of services with icons
• - Click on service type to expand details or hover over service icon to view popup bubble with details about that service
• 4. Pricing
• - Option to bundle 1(one) digital service plan and 1(one) call center service plan
• - Bundling adds 10% monthly discount to over all price
• - Customer does NOT have to bundle
• - FAQ
• 5. Contact Us
• - Include a capture form (name, company name, email, phone, message)
• - Contact info
• - Business hours
• When customer purchases their desired plan, then they are taken to a page where they must schedule a call with an account rep.
Nice to have
• home page animations
Should not have
• All information on Home/Landing page.

```html
<!DOCTYPE html>
<html lang="en">
<head>
<meta charset="utf-8">
<title>Lumora — 24x7 Live Call Answering Service</title>
<link href="https://fonts.googleapis.com/css2?family=Mulish:wght@400;600;700&family=Open+Sans:wght@400;600&display=swap" rel="stylesheet">
<style>
:root{
  --teal:#5fd3b7;
  --teal-soft:#e6f8f3;
  --navy:#1c3e4f;
  --navy-line:#2d5062;
  --ink:#222;
  --muted:#777;
  --white:#fff;
}
*{margin:0;padding:0;box-sizing:border-box}
html,body{width:731px;height:1200px;overflow:hidden;background:var(--white)}
body{position:relative;font-family:"Open Sans",sans-serif;color:var(--ink)}
.backdrop{position:absolute;inset:0}
.abs{position:absolute}
.brand{left:61px;top:36px;display:flex;align-items:center;gap:10px}
.brand-dot{width:26px;height:26px;border:2px solid var(--teal);border-radius:50%}
.brand-name{font-family:"Mulish",sans-serif;font-size:17px;letter-spacing:3px;color:#444;font-weight:400}
.nav{top:38px;left:270px;display:flex;align-items:center;height:25px}
.nav a{color:var(--white);font-size:8px;text-decoration:none;text-transform:uppercase;position:absolute;white-space:nowrap}
.nav .signup{background:var(--white);color:var(--teal);border-radius:13px;width:65px;height:25px;display:flex;align-items:center;justify-content:center;font-weight:600;font-size:8.5px}
.hero-title{left:62px;top:214px;font-family:"Mulish",sans-serif;font-weight:400;font-size:24px;line-height:31px;color:var(--ink)}
.hero-text{left:62px;top:286px;width:270px;font-size:8.5px;line-height:17px;color:var(--muted)}
.signup-form{left:62px;top:344px;width:278px;height:30px;border:1px solid #ddd;border-radius:15px;display:flex;overflow:hidden}
.signup-form span{flex:1;font-size:8px;color:#666;padding-left:19px;line-height:28px}
.signup-form b{width:99px;background:var(--teal);color:var(--white);font-size:8px;font-weight:600;display:flex;align-items:center;justify-content:center;border-radius:0 15px 15px 0}
.hero-art{left:360px;top:120px;width:360px;height:330px}
.service-icon{width:102px;height:102px;border-radius:50%;background:var(--white);box-shadow:0 4px 14px rgba(0,0,0,.08);display:flex;align-items:center;justify-content:center}
.service-icon i{display:block;width:50px;height:50px;border-radius:8px}
.service-title{font-family:"Open Sans",sans-serif;font-size:13px;font-weight:400;color:var(--ink)}
.service-text{font-size:7.5px;line-height:17.5px;color:var(--muted);width:320px}
.read-more{border:1px solid #bfeee2;border-radius:12px;color:var(--teal);font-size:7.5px;display:flex;align-items:center;justify-content:center;text-transform:uppercase}
.cta{left:90px;top:917px;width:551px;height:95px;background:var(--white);border:1px solid #e3e3e3}
.cta h2{position:absolute;left:28px;top:36px;transform:translateY(-50%);font-family:"Mulish",sans-serif;font-weight:600;font-size:18px;color:var(--ink)}
.cta p{position:absolute;left:28px;top:54px;font-family:"Mulish",sans-serif;font-size:9.5px;color:#999}
.cta .demo{position:absolute;left:382px;top:29px;width:140px;height:31px;border:2px solid var(--teal);border-radius:16px;color:var(--teal);font-family:"Mulish",sans-serif;font-size:11px;font-weight:600;display:flex;align-items:center;justify-content:center;box-shadow:0 2px 0 var(--teal)}
.social{top:1058px;left:253px;display:flex;gap:14px}
.social span{width:26px;height:26px;border-radius:50%;background:var(--navy-line)}
.social span.active{background:#2b4a8a}
.footer-rule{left:58px;top:1118px;width:615px;height:1px;background:var(--navy-line)}
.foot-icon{width:31px;height:31px;border:1.5px solid var(--white);border-radius:50%;display:flex;align-items:center;justify-content:center}
.foot-text{color:var(--white);font-size:7.5px;line-height:15px}
</style>
</head>
<body>
<svg class="backdrop" width="731" height="1200" viewBox="0 0 731 1200" aria-hidden="true">
  <path d="M0 376 L330 580 L0 952 Z" fill="var(--teal-soft)"/>
  <path d="M264 0 L731 0 L731 420 L268 84 Q232 56 264 0 Z" fill="var(--teal)"/>
  <path d="M0 996 L731 920 L731 1200 L0 1200 Z" fill="var(--navy)"/>
</svg>

<div class="abs brand"><span class="brand-dot"></span><span class="brand-name">LUMORA</span></div>

<nav class="abs nav">
  <a style="left:12px">Home</a>
  <a style="left:68px">About Us</a>
  <a style="left:138px">Services</a>
  <a style="left:205px">Pricing</a>
  <a style="left:268px">Contact Us</a>
  <a class="signup" style="left:336px">Sign Up</a>
</nav>

<h1 class="abs hero-title">24x7 Live Call<br>Answering Service</h1>
<p class="abs hero-text">Sed ut perspiciatis unde omnis iste natus error sit voluptatem accusantium doloremque laudanttam rem aperiam,</p>
<div class="abs signup-form"><span>Enter Email..</span><b>SIGN UP FOR FREE</b></div>

<div class="abs hero-art" role="img" aria-label="Isometric illustration of a team meeting around a table with a presentation board" style="background:linear-gradient(160deg,#c9f1ea 0%,#a8e8df 55%,#d9dede 100%);clip-path:polygon(0 62%,62% 8%,100% 62%,68% 100%)"></div>

<div class="abs service-icon" style="left:207px;top:527px"><i role="img" aria-label="Digital services icon with phone and growth chart" style="background:linear-gradient(135deg,#6d7f8c,#f2c94c)"></i></div>
<h3 class="abs service-title" style="left:339px;top:528px">Digital Services</h3>
<p class="abs service-text" style="left:340px;top:554px">Sed ut perspiciatis unde omnis iste natus error sit voluptatem accusantium dolorem-que laudantiumotam rem aperiaeaque ipsa quae..</p>
<div class="abs read-more" style="left:340px;top:601px;width:70px;height:24px">Read More</div>

<div class="abs service-icon" style="left:118px;top:694px"><i role="img" aria-label="Call center agent with headset and speech bubbles" style="background:linear-gradient(135deg,#e85a4f,#f5b942 60%,#3a3a3a)"></i></div>
<h3 class="abs service-title" style="left:250px;top:695px">Call Center Services</h3>
<p class="abs service-text" style="left:251px;top:721px">Sed ut perspiciatis unde omnis iste natus error sit voluptatem accusantium dolorem-que laudantiumotam rem aperiaeaque ipsa quae..</p>
<div class="abs read-more" style="left:251px;top:768px;width:71px;height:24px">Read More</div>

<section class="abs cta">
  <h2>Get your call center up and running</h2>
  <p>Create numbers in 40+ countries instantly</p>
  <div class="demo">Request A Demo</div>
</section>

<div class="abs social" aria-label="Social links">
  <span class="active"></span><span></span><span></span><span></span><span></span><span></span>
</div>
<div class="abs footer-rule"></div>

<div class="abs foot-icon" style="left:59px;top:1146px">
  <svg width="14" height="13" viewBox="0 0 14 13"><path d="M7 1 L13 6.5 H11 V12 H8.5 V8.5 H5.5 V12 H3 V6.5 H1 Z" fill="var(--white)"/></svg>
</div>
<p class="abs foot-text" style="left:102px;top:1144px">Lumora, Inc.<br>418 Alder Crest Way, Lakeview, CA 90210</p>

<div class="abs foot-icon" style="left:268px;top:1146px">
  <svg width="13" height="13" viewBox="0 0 24 24"><path d="M6.6 10.8a15 15 0 006.6 6.6l2.2-2.2c.3-.3.7-.4 1-.2 1.1.4 2.3.6 3.6.6.6 0 1 .4 1 1V20c0 .6-.4 1-1 1A17 17 0 013 4c0-.6.4-1 1-1h3.5c.6 0 1 .4 1 1 0 1.3.2 2.5.6 3.6.1.3 0 .7-.2 1z" fill="var(--white)"/></svg>
</div>
<p class="abs foot-text" style="left:311px;top:1154px">Phone : (800) 555-0147</p>

<p class="abs foot-text" style="right:60px;top:1154px">© copyright 2018 Lumora, Inc.All Rights Reserved &nbsp;|&nbsp; Privacy policy</p>
</body>
</html>
```